Eyecatching website design for commercial lighting business

This contest is all about the graphic design aspect. We need a striking website design for a commercial lighting company. We want something really eye catching to introduce people to our range of induction and LED lights which save businesses money on maintenance and electricity costs.

To be successful in this contest you will need to provide a design and pictures for the pages listed below.

We are using the platform velbrin.com.au and you can see the attached template which everything will be loaded into so we just need HTML files which we can upload and we can do everything else from Velbrin.

The final design should be strong and clean and use the colours and textures in the attached business card file.

Detailed requirements:

Please see attached screenshot of the website template, all we need is a fantastic graphic design and improvement/ incorporation of our logo for the following pages
Page Headings:
1. Home
About Us, Contact Us, snapshot of and link to Blog

Each of the below pages will have several paragraphs of text followed by a list of suitable products which is generated from our product catalogue.

2. Car Park Lighting
3. Educational Lighting
4. Hospitality Lighting
5. Office & Shop Lighting
6. Warehouse Lighting

Some of the website we have seen which are similar in nature are:
http://www.quorvanlamps.com.au/
http://www.tibrox.com/
http://www.gandowlumen.net/commercial-led
but we really want a modern, eye catching and memorable design

Some of the designs built on Velbrin that we like are:

http://www.pemberhollow.com.au/
http://www.marwickgoods.com.au/
http://www.kelmorabay.com.au/

I've also uploaded a couple of photos that we love. We'd like something similar for each industry.

Target Market(s)

Company Owners, Maintenance & Facilities Managers, Electrical Contractors

Industry/Entity Type

Electrical

Coding

Coded - Design and coding required

Number of Pages Required

5+ page

Font styles to use
Sans Serif

Colors
33a6d7
ec1f27

Requirements
Must have
• -Must scale to mobile
• -HTML coded files need to be provided (HTML Bootstrap)
Nice to have
• -Prefer incorporation of our logo into header bar
• -Design of 2-3 advertising banners which can be displayed on the home page
• -Prominent call to action button towards top of page 'Get a quote' or similar
• -Grid based design HTML Bootstrap

```html
<!DOCTYPE html>
<html lang="en">
<head>
<meta charset="utf-8">
<title>Halden Lighting – Commercial Lighting</title>
<link href="https://fonts.googleapis.com/css2?family=Roboto:wght@400;500;700&family=Roboto+Condensed:wght@400;700&display=swap" rel="stylesheet">
<style>
:root{
  --blue:#33a6d7;
  --blue-btn:#2f6fd6;
  --red:#ec1f27;
  --dark:#222426;
  --header:#2a2c2f;
  --grey-bg:#eeeeee;
  --text:#555;
  --heading:#222;
  --white:#fff;
}
*{margin:0;padding:0;box-sizing:border-box}
html,body{width:1200px;height:2452px;overflow:hidden}
body{font-family:"Roboto",Arial,sans-serif;color:var(--text);background:var(--white);position:relative}
.condensed{font-family:"Roboto Condensed","Arial Narrow",sans-serif}

/* Header */
.site-header{position:absolute;top:0;left:0;width:1200px;height:160px;background:var(--header)}
.topbar{position:absolute;top:16px;right:80px;display:flex;align-items:center;gap:10px;color:#ddd;font-size:15px}
.topbar svg{width:18px;height:18px}
.topbar strong{color:var(--white);font-weight:700;font-size:17px}
.brand{position:absolute;left:80px;top:56px;display:flex;align-items:center;gap:14px}
.brand-mark{width:40px;height:40px;border-radius:50%;background:var(--blue)}
.brand-name{font-family:"Roboto Condensed","Arial Narrow",sans-serif;font-weight:700;font-size:26px;color:var(--red);letter-spacing:1px;text-transform:uppercase}
.main-nav{position:absolute;right:80px;top:98px;display:flex;gap:52px}
.main-nav a{color:var(--white);text-decoration:none;font-size:15px;font-weight:500;text-transform:uppercase;letter-spacing:.5px}

/* Hero */
.hero{position:absolute;top:160px;left:0;width:1200px;height:568px;overflow:hidden}
.hero-photo{position:absolute;inset:0;background:radial-gradient(ellipse at 72% 45%,#4b8a3a 0%,#1f4a22 30%,#0c160d 62%,#050805 100%)}
.hero-copy{position:absolute;left:100px;top:228px}
.hero-title{font-family:"Roboto Condensed","Arial Narrow",sans-serif;font-weight:700;color:var(--white);font-size:56px;line-height:72px;text-transform:uppercase;letter-spacing:1px}
.hero-title span{background:rgba(0,0,0,.55);padding:0 10px;-webkit-box-decoration-break:clone;box-decoration-break:clone}
.btn{display:inline-block;color:var(--white);text-decoration:none;font-size:15px;font-weight:500;text-transform:uppercase;letter-spacing:.5px;padding:12px 26px;border-radius:3px}
.btn-blue{background:var(--blue-btn)}
.btn-red{background:var(--red)}
.hero .btn{margin-top:28px;margin-left:4px}
.hero-arrow{position:absolute;top:250px;width:40px;height:60px}
.hero-arrow.prev{left:20px}
.hero-arrow.next{right:20px}

/* Welcome */
.welcome{position:absolute;top:728px;left:0;width:1200px;height:352px;text-align:center;padding-top:62px}
.section-title{font-size:30px;font-weight:700;color:var(--heading)}
.welcome .company{color:var(--red);font-size:30px;font-weight:700;margin-top:8px}
.welcome p{width:900px;margin:28px auto 0;font-size:15px;line-height:26px}
.welcome .btn{margin-top:22px;padding:10px 24px;font-size:14px}

/* Solutions */
.solutions{position:absolute;top:1080px;left:0;width:1200px;height:500px;background:var(--grey-bg);text-align:center;padding-top:48px}
.solution-grid{display:flex;gap:64px;margin:44px 0 0 80px;width:1040px}
.solution-card{width:212px;text-align:center}
.solution-photo{width:212px;height:150px;border:6px solid var(--white);box-shadow:0 1px 3px rgba(0,0,0,.15)}
.solution-card h3{color:var(--blue);font-size:19px;font-weight:700;text-transform:uppercase;margin-top:26px;font-family:"Roboto Condensed","Arial Narrow",sans-serif}
.solution-card p{font-size:13px;line-height:19px;margin-top:8px;padding:0 10px}
.read-more{display:inline-block;margin-top:12px;font-size:13px;font-weight:700;color:var(--heading);text-decoration:none;text-transform:uppercase}

/* Video */
.videos{position:absolute;top:1580px;left:0;width:1200px;height:420px;overflow:hidden}
.videos-bg{position:absolute;inset:0;background:linear-gradient(100deg,#0d1a33 0%,#1d3f7a 45%,#2a5fa8 70%,#c9a24a 100%)}
.video-frame{position:absolute;left:80px;top:52px;width:512px;height:330px;background:var(--white);padding:8px}
.video-thumb{position:relative;width:100%;height:100%;background:radial-gradient(circle at 50% 50%,#f4f1e6 0%,#d9d4c2 50%,#9f9a8a 100%)}
.video-play{position:absolute;left:50%;top:50%;width:78px;height:78px;margin:-39px 0 0 -39px}
.video-copy{position:absolute;left:632px;top:90px;width:480px;color:var(--white)}
.video-copy h2{font-size:40px;font-weight:500}
.video-copy p{font-size:15px;line-height:24px;margin-top:18px}
.video-copy .btn{margin-top:26px;font-size:14px;padding:11px 24px}

/* Blog */
.blog{position:absolute;top:2000px;left:0;width:1200px;height:360px;text-align:center;padding-top:104px}
.blog-grid{display:flex;gap:60px;margin:36px 0 0 80px;width:1040px;text-align:left}
.blog-post{width:490px;display:flex;gap:22px}
.blog-photo{width:112px;height:120px;flex:none;background:linear-gradient(180deg,#d7dde4,#8a97a6)}
.blog-post h3{color:var(--blue);font-size:17px;font-weight:700;font-family:"Roboto Condensed","Arial Narrow",sans-serif}
.blog-post time{display:block;font-size:12px;color:#999;margin-top:4px}
.blog-post p{font-size:13px;line-height:19px;margin-top:8px}
.blog-post .read-more{margin-top:8px}

/* Footer */
.site-footer{position:absolute;top:2360px;left:0;width:1200px;height:92px;background:var(--dark);display:flex;align-items:center;justify-content:space-between;padding:0 80px}
.site-footer small{color:#ccc;font-size:14px}
.social{display:flex;gap:10px}
.social span{width:32px;height:32px;border-radius:50%;background:var(--white)}
</style>
</head>
<body>

<header class="site-header">
  <div class="topbar">
    <svg viewBox="0 0 24 24" fill="#ddd"><path d="M6.6 10.8a15.1 15.1 0 0 0 6.6 6.6l2.2-2.2c.3-.3.7-.4 1-.2 1.1.4 2.3.6 3.6.6.6 0 1 .4 1 1V20c0 .6-.4 1-1 1A17 17 0 0 1 3 4c0-.6.4-1 1-1h3.5c.6 0 1 .4 1 1 0 1.3.2 2.5.6 3.6.1.3 0 .7-.2 1z"/></svg>
    <span>Call us</span><strong>1800 472 316</strong>
  </div>
  <div class="brand">
    <span class="brand-mark"></span>
    <span class="brand-name">Halden Lighting</span>
  </div>
  <nav class="main-nav">
    <a href="#">Home</a>
    <a href="#">Commercial LED</a>
    <a href="#">Request a Quote</a>
    <a href="#">About</a>
    <a href="#">Contact Us</a>
  </nav>
</header>

<section class="hero">
  <div class="hero-photo" role="img" aria-label="Close-up of energy saving LED and induction light bulbs glowing against a dark green background"></div>
  <svg class="hero-arrow prev" viewBox="0 0 40 60"><polyline points="28,10 10,30 28,50" fill="none" stroke="#fff" stroke-width="5"/></svg>
  <svg class="hero-arrow next" viewBox="0 0 40 60"><polyline points="12,10 30,30 12,50" fill="none" stroke="#fff" stroke-width="5"/></svg>
  <div class="hero-copy">
    <h1 class="hero-title"><span>The best range of energy</span><br><span>saving commercial &amp; industrial</span><br><span>lighting</span></h1>
    <a class="btn btn-blue" href="#">Find out more</a>
  </div>
</section>

<section class="welcome">
  <h2 class="section-title">Welcome to the Commercial Lighting Division of</h2>
  <div class="company">K&amp;R Halden Business Solutions</div>
  <p>Retrofitting the lighting in a commercial or industrial premises is a great way to save money on energy costs and maintenance, create a safer work environment and reduce the load on the wiring in the premises. When you are considering a retrofit of a commercial building there are a number of technologies on the market and a lot to consider.</p>
  <a class="btn btn-red" href="#">Read more</a>
</section>

<section class="solutions">
  <h2 class="section-title">We provide these lighting solutions</h2>
  <div class="solution-grid">
    <article class="solution-card">
      <div class="solution-photo" role="img" aria-label="Underground car park lit by bright ceiling lights" style="background:linear-gradient(180deg,#e9ecef,#9aa3ab)"></div>
      <h3>Car Park Lighting</h3>
      <p>Neque porro quisquam est qui dolorem ipsum quia dolor sit amet, consectetur, adipisci velit.</p>
      <a class="read-more" href="#">Read more</a>
    </article>
    <article class="solution-card">
      <div class="solution-photo" role="img" aria-label="Child in a classroom under bright lighting" style="background:linear-gradient(180deg,#e8d6bf,#a8826a)"></div>
      <h3>Educational Lighting</h3>
      <p>Neque porro quisquam est qui dolorem ipsum quia dolor sit amet, consectetur, adipisci velit.</p>
      <a class="read-more" href="#">Read more</a>
    </article>
    <article class="solution-card">
      <div class="solution-photo" role="img" aria-label="Hotel corridor with red accents and ceiling lights" style="background:linear-gradient(180deg,#f2f2f2,#c9b3b3)"></div>
      <h3>Hospitality Lighting</h3>
      <p>Neque porro quisquam est qui dolorem ipsum quia dolor sit amet, consectetur, adipisci velit.</p>
      <a class="read-more" href="#">Read more</a>
    </article>
    <article class="solution-card">
      <div class="solution-photo" role="img" aria-label="Open plan office with desks and panel lights" style="background:linear-gradient(180deg,#eef1f4,#aab4be)"></div>
      <h3>Office Lighting</h3>
      <p>Neque porro quisquam est qui dolorem ipsum quia dolor sit amet, consectetur, adipisci velit.</p>
      <a class="read-more" href="#">Read more</a>
    </article>
  </div>
</section>

<section class="videos">
  <div class="videos-bg" role="img" aria-label="Blurred blue and gold lights in the background"></div>
  <div class="video-frame">
    <div class="video-thumb" role="img" aria-label="Video still of LED corn light bulbs">
      <svg class="video-play" viewBox="0 0 78 78"><circle cx="39" cy="39" r="37" fill="rgba(0,0,0,.55)" stroke="#fff" stroke-width="3"/><polygon points="31,24 56,39 31,54" fill="#fff"/></svg>
    </div>
  </div>
  <div class="video-copy">
    <h2>Featured Video's</h2>
    <p>Lorem ipsum dolor sit amet, consectetur adipiscing elit, sed do eiusmod tempor incididunt ut labore et dolore magna aliqua. Ut enim ad minim veniam, quis nostrud exercitation ullamco laboris nisi ut aliquip ex ea commodo consequat.</p>
    <a class="btn btn-red" href="#">View all videos</a>
  </div>
</section>

<section class="blog">
  <h2 class="section-title">Blog Post</h2>
  <div class="blog-grid">
    <article class="blog-post">
      <div class="blog-photo" role="img" aria-label="Portrait photo of the post author"></div>
      <div>
        <h3>de Finibus Bonorum et Malorum</h3>
        <time>December 14, 2015</time>
        <p>Lorem ipsum dolor sit amet, consectetur adipiscing elit, sed do eiusmod tempor incididunt ut labore et dolore.</p>
        <a class="read-more" href="#">Read more</a>
      </div>
    </article>
    <article class="blog-post">
      <div class="blog-photo" role="img" aria-label="Portrait photo of the post author"></div>
      <div>
        <h3>de Finibus Bonorum et Malorum</h3>
        <time>December 14, 2015</time>
        <p>Lorem ipsum dolor sit amet, consectetur adipiscing elit, sed do eiusmod tempor incididunt ut labore et dolore.</p>
        <a class="read-more" href="#">Read more</a>
      </div>
    </article>
  </div>
</section>

<footer class="site-footer">
  <small>Copyright © 2015, Yoursite All rights reserved</small>
  <div class="social"><span></span><span></span><span></span><span></span><span></span><span></span></div>
</footer>

</body>
</html>
```